Catering Company Website Design

We are working with a bbq catering company in California called Ember Plank Catering.
Some sites to use for content/competitors and inspiration:
https://19parsnips.com
https://mbetrovandel.com
https://ridgefeastco.com
https://tinforkdenvale.com (client's favorite)
https://www.marvenasmokehut.com (client's favorite)
https://www.theopenkettlekitchen.com
Thank you for taking the time to consider designing a website for us. We are web developers based in Stockton, CA, USA. Most of our projects go through the same process. Understanding this process may help you win a project with us. We custom-code all of our websites in-house. We don’t have any requirements as to what tools you use for your design, but we prefer Figma files. For any design that we label as four-stars, we send it to the client for review. The client picks the final design they want us to use. Once we complete this process, we will continue to show additional clients all the four-star sites and purchase them later. Your designs will have multiple chances to sell. For better chances of success, we ask that you follow these guidelines.
IMAGES:
If you use any images or icons in the design, we ask that you have a link to the asset so we can purchase the image/icon. Most of the designs we submit do not have the customer’s images on them unless they have some great images. Be creative; show us the feeling you are trying to portray with your image choices. Use any royalty-free site you choose. We subscribe to Zelvio and mainly use their images, but we can purchase images outside of Zelvio.
PLEASE NOTE: we will not submit designs to clients with watermarks on the images.
FONTS:
We ask that you identify the fonts used in the design. This can be done in a message if you want. We typically use Google Fonts and Zelvio Fonts.
CONTENT:
We're always open to different content and ideas. We often submit designs with stock images so the client can see our vision. We typically take pictures after the website launch to use their images with our vision. Lorem Ipsum is fine for paragraphs, but we ask that you write the headers in correct English. We want to be able to show the vision and identify the sections of the website.
INSPIRATION:
We typically add a couple of links in the brief of websites we like to help you get started in your design.
REVISIONS:
We do not often ask for revisions of the designs unless we see something in the design that may not appeal to the client. If there are slight changes that we want to make, we do that in the development process.
FEEDBACK:
We rarely give feedback on designs during the design process. We are working on many website projects and do not have the time to provide feedback. We usually respond if your request is well thought out and asks specific questions, but a note asking “feedback, please” usually goes unanswered

```html
<!DOCTYPE html>
<html lang="en">
<head>
<meta charset="utf-8">
<title>Ember Plank Catering</title>
<link rel="stylesheet" href="https://fonts.googleapis.com/css2?family=Alegreya:wght@500;700&family=Oswald:wght@300;400;500&display=swap">
<style>
:root{
  --red:#d3282a;
  --red-dark:#b51f22;
  --brown:#4b1810;
  --brown-head:#5b1d14;
  --text:#6f6a68;
  --white:#ffffff;
  --shadow:0 10px 40px rgba(0,0,0,.10);
}
*{box-sizing:border-box;margin:0;padding:0}
html,body{width:1200px;height:4942px;overflow:hidden;background:var(--white)}
body{font-family:"Oswald",sans-serif;color:var(--text)}
.page{position:relative;width:1200px;height:4942px;overflow:hidden}
.abs{position:absolute}
.photo{position:absolute;display:block}
.btn{position:absolute;display:flex;align-items:center;justify-content:center;background:var(--red);color:var(--white);font:400 15px/1 "Oswald",sans-serif;text-transform:uppercase;height:46px;width:132px;text-decoration:none}
.btn--light{background:var(--white);color:var(--red)}
.heading{position:absolute;font-family:"Alegreya",serif;font-weight:500;color:var(--brown-head);text-transform:uppercase;font-size:56px;letter-spacing:2px;line-height:1}
.copy{position:absolute;font:300 16.5px/32px "Oswald",sans-serif;color:var(--text);text-align:justify}

/* header */
.site-header{position:absolute;top:0;left:0;width:1200px;height:90px;background:var(--white);z-index:5}
.brand{position:absolute;left:142px;top:-40px;width:232px;height:232px;border-radius:50%;background:var(--white);z-index:6;display:flex;align-items:flex-end;justify-content:center;padding-bottom:48px}
.brand__name{font:500 21px/1.1 "Oswald",sans-serif;color:var(--brown);text-transform:uppercase;text-align:center;width:180px}
.nav{position:absolute;top:40px;left:440px;display:flex;gap:0;z-index:7}
.nav a{position:absolute;font:500 13px/1 "Oswald",sans-serif;color:#222;text-transform:uppercase;text-decoration:none;white-space:nowrap}
.nav a.is-active{color:var(--red)}
.nav-search{position:absolute;left:912px;top:40px;z-index:7}
.order-btn{position:absolute;left:950px;top:0;width:106px;height:90px;background:var(--red);color:var(--white);font:400 14px/1 "Oswald",sans-serif;text-transform:uppercase;display:flex;align-items:center;justify-content:center;z-index:7}

/* hero */
.hero-photo{top:90px;left:0;width:1200px;height:650px;background:linear-gradient(130deg,#1c120d 0%,#4a2414 30%,#8a3d18 55%,#d0741f 78%,#f3b04a 100%)}
.hero-dots{right:74px;top:324px}
.hero-dots span{display:block;width:10px;height:10px;border-radius:50%;background:var(--white);margin-bottom:24px}
.hero-title{position:absolute;left:0;width:1200px;text-align:center;font-family:"Alegreya",serif;font-weight:500;font-size:58px;letter-spacing:2px;line-height:1;z-index:3}
.hero-sub{position:absolute;left:0;width:1200px;top:535px;text-align:center;color:var(--white);font:400 22px/1 "Oswald",sans-serif;text-transform:uppercase;z-index:3}

/* services */
.service{position:absolute;top:1306px;height:432px;overflow:hidden}
.service__box{position:absolute;background:var(--white);padding:36px 40px 0;border-top-left-radius:50px}
.service__box--red{background:var(--red);color:var(--white)}
.service__title{font:500 17px/1 "Oswald",sans-serif;text-transform:uppercase;color:#222;margin-bottom:10px}
.service__text{font:300 13.5px/22px "Oswald",sans-serif;text-align:justify}
.service__box--red .service__title,.service__box--red .service__text{color:var(--white)}

.card{position:absolute;background:var(--white);box-shadow:var(--shadow)}

/* cta */
.cta-photo{top:3160px;left:0;width:1200px;height:540px;background:linear-gradient(110deg,#b9737a 0%,#7d4638 28%,#3b2a24 50%,#7a3526 72%,#a44a32 100%)}
.cta-card{left:284px;top:3277px;width:657px;height:304px;background:var(--white);border-top-right-radius:80px;text-align:center}

/* events */
.event-photo{top:3903px;width:451px;height:344px}
.event-date{position:absolute;top:3926px;width:44px;height:64px;background:var(--red);color:var(--white);font:500 14px/17px "Oswald",sans-serif;text-align:center;padding-top:14px}
.event-title{position:absolute;top:4276px;font:500 19px/1 "Oswald",sans-serif;color:#222;text-transform:uppercase}
.arrow{position:absolute;top:4051px;width:46px;height:46px;border-radius:50%;border:1px solid #bbb;background:var(--white);display:flex;align-items:center;justify-content:center}

/* footer */
.footer-bg{top:4560px;left:0;width:1200px;height:382px}
.footer-label{position:absolute;font:500 16px/24px "Oswald",sans-serif;color:var(--white);text-transform:uppercase}
.footer-input{position:absolute;left:422px;top:4768px;width:177px;height:34px;background:var(--white);font:300 12px/34px "Oswald",sans-serif;color:#555;padding-left:14px}
.footer-signup{position:absolute;left:599px;top:4768px;width:98px;height:34px;background:var(--red);color:var(--white);font:500 14px/34px "Oswald",sans-serif;text-align:center;text-transform:uppercase}
.social{position:absolute;top:4822px;width:30px;height:30px;border-radius:50%;border:2px solid var(--white)}
.footer-contact{position:absolute;left:860px;font:300 14px/20px "Oswald",sans-serif;color:var(--white)}
.footer-copy{position:absolute;top:4890px;left:0;width:1200px;text-align:center;font:300 14px/1 "Oswald",sans-serif;color:var(--white)}
</style>
</head>
<body>
<div class="page">

  <!-- header -->
  <header class="site-header"></header>
  <div class="brand"><span class="brand__name">Ember Plank Catering</span></div>
  <nav class="nav">
    <a class="is-active" style="left:0">Home</a>
    <a style="left:64px">Menu</a>
    <a style="left:128px">Reservations</a>
    <a style="left:241px">Catering</a>
    <a style="left:327px">Shop</a>
    <a style="left:389px">Contact</a>
  </nav>
  <svg class="nav-search" width="16" height="16" viewBox="0 0 16 16" aria-hidden="true"><circle cx="6.5" cy="6.5" r="5" fill="none" stroke="#222" stroke-width="2"/><line x1="10.2" y1="10.2" x2="15" y2="15" stroke="#222" stroke-width="2.4"/></svg>
  <a class="order-btn">Order Online</a>

  <!-- hero -->
  <div class="photo hero-photo" role="img" aria-label="Sausages sizzling on a flaming grill"></div>
  <div class="abs hero-dots"><span></span><span></span></div>
  <svg class="abs" style="left:0;top:280px;z-index:2" width="1200" height="480" viewBox="0 280 1200 480" aria-hidden="true">
    <circle cx="600" cy="548" r="250" fill="rgba(88,24,14,.9)"/>
    <path d="M0,500 Q600,790 1200,500 L1200,560 Q600,844 0,560 Z" fill="var(--red)"/>
    <path d="M0,560 Q600,844 1200,560 L1200,760 L0,760 Z" fill="#fff"/>
    <path d="M0,574 Q600,866 1200,574" fill="none" stroke="var(--red)" stroke-width="3"/>
  </svg>
  <div class="hero-title" style="top:404px;color:var(--white)">Ember Plank</div>
  <div class="hero-title" style="top:462px;color:var(--red)">Catering</div>
  <div class="hero-sub">Food is only the beginning</div>
  <a class="btn" style="left:533px;top:582px;width:134px;z-index:3">Order Online</a>

  <!-- decorative food cut-outs -->
  <div class="photo" style="left:8px;top:642px;width:220px;height:145px;border-radius:50%;background:radial-gradient(#b9452a,#e5c08a 70%,rgba(255,255,255,0) 72%)" role="img" aria-label="Grilled sausage in a bun with peppers"></div>

  <!-- welcome -->
  <h1 class="heading" style="left:146px;top:800px">Welcome</h1>
  <p class="copy" style="left:146px;top:878px;width:465px">Sed ut perspiciatis unde omnis iste natus error sit voluptatem accusantium doloremque laudantium, totam rem aperiam, eaque ipsa quae ab illo inventore veritatis et quasi architecto beatae vitae dicta sunt explicabo. Nemo enim ipsam voluptatem quia voluptas sit aspernatur aut odit aut fugit, sed quia consequuntur magni dolores eos qui ratione voluptatem sequi nesciunt. Neque porro quisquam est, qui dolorem ipsum quia dolor sit amet, consectetur, adipisci velit, sed quia non numquam eius modi tempora incidunt ut labore et dolore magnam aliquam quaerat non numquam eius modi voluptatem.</p>
  <a class="btn" style="left:146px;top:1160px">Read More</a>
  <div class="abs" style="left:902px;top:766px;width:178px;height:190px;background:var(--red);border-top-right-radius:60px"></div>
  <div class="photo" style="left:653px;top:793px;width:400px;height:334px;border-top-right-radius:60px;background:linear-gradient(140deg,#4a3a30,#1f1a17 45%,#7a3018 65%,#3a2a22)" role="img" aria-label="Sausages in a cast iron pan with rosemary"></div>
  <div class="photo" style="left:680px;top:1125px;width:340px;height:200px;background:radial-gradient(ellipse 48% 28% at 50% 25%,#a8401f 90%,rgba(255,255,255,0) 92%),linear-gradient(#fff0,#fff0)" role="img" aria-label="Grilled sausage on a fork"></div>
  <div class="photo" style="left:1080px;top:1112px;width:118px;height:196px;border-radius:50%;background:radial-gradient(#d62a22,#a51812 60%,rgba(255,255,255,0) 62%)" role="img" aria-label="Red chili peppers"></div>

  <!-- services -->
  <div class="service" style="left:0;width:392px;border-top-left-radius:70px">
    <div class="photo" style="inset:0;background:linear-gradient(150deg,#3a2a22,#8d6a52 45%,#c9a78a 70%,#5a4030)" role="img" aria-label="Catered event plates being served"></div>
    <div class="service__box" style="left:25px;top:303px;width:336px;height:140px">
      <h3 class="service__title">Catered Events</h3>
      <p class="service__text">Sed ut perspiciatis unde omnis iste natus error sit voluptatem accusantium doloremque laudantium, totam rem aperiam, eaque ipsa quae</p>
    </div>
  </div>
  <a class="btn" style="left:67px;top:1766px">Read More</a>

  <div class="service" style="left:400px;width:400px;height:506px;border-radius:70px 70px 0 0;overflow:visible">
    <div class="photo" style="left:0;top:0;width:400px;height:432px;border-radius:70px 70px 0 0;background:linear-gradient(160deg,#3a2c24,#7a5a40 45%,#b88a58 65%,#3c2a20)" role="img" aria-label="Colleagues sharing a workplace meal"></div>
    <div class="service__box service__box--red" style="left:32px;top:299px;width:336px;height:207px">
      <h3 class="service__title">Workplace Dining</h3>
      <p class="service__text">Sed ut perspiciatis unde omnis iste natus error sit voluptatem accusantium doloremque laudantium, totam rem aperiam, eaque ipsa quae</p>
    </div>
  </div>
  <a class="btn btn--light" style="left:463px;top:1749px">Read More</a>

  <div class="service" style="left:808px;width:392px;border-top-left-radius:70px">
    <div class="photo" style="inset:0;background:linear-gradient(140deg,#6a2a18,#b4482a 40%,#8a3018 65%,#5a2a18)" role="img" aria-label="Grilled sausages on a wooden board"></div>
    <div class="service__box" style="left:33px;top:303px;width:334px;height:140px">
      <h3 class="service__title">Delivery</h3>
      <p class="service__text">Sed ut perspiciatis unde omnis iste natus error sit voluptatem accusantium doloremque laudantium, totam rem aperiam, eaque ipsa quae</p>
    </div>
  </div>
  <a class="btn" style="left:881px;top:1766px">Read More</a>

  <!-- our story -->
  <div class="photo" style="left:985px;top:1868px;width:215px;height:150px;border-radius:50%;background:radial-gradient(#d22a22,#a51a14 55%,rgba(255,255,255,0) 58%)" role="img" aria-label="Red chili peppers"></div>
  <div class="abs" style="left:117px;top:1897px;width:178px;height:177px;background:var(--red);border-top-left-radius:60px"></div>
  <div class="photo" style="left:146px;top:1922px;width:455px;height:399px;border-top-right-radius:70px;background:linear-gradient(150deg,#7a5a44,#2a2420 40%,#5a4a3a 60%,#a08060)" role="img" aria-label="Burgers and vegetables on a round grill"></div>
  <div class="card" style="left:528px;top:2079px;width:524px;height:398px;border-top-left-radius:70px"></div>
  <h2 class="heading" style="left:597px;top:2165px">Our Story</h2>
  <p class="copy" style="left:597px;top:2232px;width:402px">Sed ut perspiciatis unde omnis iste natus error sit voluptatem accusantium doloremque laudantium, totam rem aperiam, eaque ipsa quae ab illo inventore veritatis et quasi architecto beatae vitae dicta sunt explicabo. Nemo enim ipsam voluptatem</p>
  <a class="btn" style="left:601px;top:2381px">Read More</a>

  <!-- our food -->
  <div class="photo" style="left:54px;top:2419px;width:330px;height:280px;background:radial-gradient(ellipse 50% 22% at 50% 22%,#a8401f 92%,rgba(255,255,255,0) 94%)" role="img" aria-label="Grilled sausage on a fork"></div>
  <div class="abs" style="left:904px;top:2556px;width:179px;height:190px;background:var(--red);border-top-right-radius:20px"></div>
  <div class="photo" style="left:601px;top:2580px;width:453px;height:398px;border-top-left-radius:70px;background:linear-gradient(150deg,#d9cfc4,#c99a5a 40%,#8fae6a 60%,#ece6e0)" role="img" aria-label="Croissant sandwich with cucumber and ham"></div>
  <div class="card" style="left:144px;top:2698px;width:522px;height:399px;border-top-right-radius:70px"></div>
  <h2 class="heading" style="left:217px;top:2785px">Our Food</h2>
  <p class="copy" style="left:213px;top:2852px;width:400px">Sed ut perspiciatis unde omnis iste natus error sit voluptatem accusantium doloremque laudantium, totam rem aperiam, eaque ipsa quae ab illo inventore veritatis et quasi architecto beatae vitae dicta sunt explicabo. Nemo enim ipsam voluptatem</p>
  <a class="btn" style="left:213px;top:2999px">Read More</a>

  <!-- call to action -->
  <div class="photo cta-photo" role="img" aria-label="Assorted cured meats and sausages"></div>
  <div class="abs cta-card"></div>
  <h2 class="heading" style="left:284px;top:3370px;width:657px;text-align:center;font-size:54px;line-height:58px">Ready to plan your<br>unique experience?</h2>
  <a class="btn" style="left:547px;top:3498px;width:135px">Contact Us</a>

  <!-- latest events -->
  <div class="photo" style="left:960px;top:3726px;width:215px;height:120px;border-radius:40%;background:radial-gradient(#c9485a,#8a2a30 60%,rgba(255,255,255,0) 63%)" role="img" aria-label="Sliced salami"></div>
  <h2 class="heading" style="left:0;top:3820px;width:1228px;text-align:center">Latest Events</h2>
  <a class="arrow" style="left:75px" aria-label="Previous"><svg width="12" height="14" viewBox="0 0 12 14"><path d="M8 1 L2 7 L8 13" fill="none" stroke="#222" stroke-width="2"/></svg></a>
  <a class="arrow" style="left:1077px" aria-label="Next"><svg width="12" height="14" viewBox="0 0 12 14"><path d="M4 1 L10 7 L4 13" fill="none" stroke="#222" stroke-width="2"/></svg></a>

  <div class="photo event-photo" style="left:146px;background:linear-gradient(150deg,#5a6068,#8a6a58 45%,#3a3230 70%,#6a625c)" role="img" aria-label="Friends sharing grilled sausages at an event"></div>
  <svg class="abs" style="left:202px;top:3945px" width="340" height="262" viewBox="0 0 340 262" aria-hidden="true"><rect x="1" y="1" width="338" height="260" fill="none" stroke="#fff" stroke-width="2"/><path d="M170 118 V144 M157 131 H183" stroke="#fff" stroke-width="3"/></svg>
  <div class="event-date" style="left:516px">SEP<br>2024</div>
  <h3 class="event-title" style="left:171px">Uasi architecto beatae vitae</h3>
  <p class="copy" style="left:171px;top:4310px;width:400px">Sed ut perspiciatis unde omnis iste natus error sit voluptatem accusantium doloremque laudantium, totam rem aperiam, eaque ipsa quae ab illo inventore veritatis et quasi architecto</p>
  <a class="btn" style="left:171px;top:4426px">Read More</a>

  <div class="photo event-photo" style="left:603px;background:linear-gradient(150deg,#2a1e18,#6a3a24 45%,#a0502c 65%,#3a241a)" role="img" aria-label="Chef preparing fresh sausages"></div>
  <div class="event-date" style="left:974px">SEP<br>2024</div>
  <h3 class="event-title" style="left:628px">Uasi architecto beatae vitae</h3>
  <p class="copy" style="left:628px;top:4310px;width:400px">Sed ut perspiciatis unde omnis iste natus error sit voluptatem accusantium doloremque laudantium, totam rem aperiam, eaque ipsa quae ab illo inventore veritatis et quasi architecto</p>
  <a class="btn" style="left:628px;top:4426px">Read More</a>

  <!-- footer -->
  <svg class="abs" style="left:0;top:4540px" width="1200" height="402" viewBox="0 0 1200 402" aria-hidden="true">
    <path d="M0,150 Q600,-70 1200,150 L1200,402 L0,402 Z" fill="var(--red)"/>
    <path d="M0,170 Q600,-30 1200,170 L1200,402 L0,402 Z" fill="#fff"/>
    <path d="M0,190 Q600,0 1200,190 L1200,402 L0,402 Z" fill="var(--brown)"/>
  </svg>
  <div class="photo" style="left:0;top:4540px;width:160px;height:140px;border-radius:50%;background:radial-gradient(#b9452a,#e5c08a 65%,rgba(255,255,255,0) 68%)" role="img" aria-label="Grilled sausage in a bun with peppers"></div>
  <div class="photo" style="left:1080px;top:4495px;width:120px;height:200px;border-radius:50%;background:radial-gradient(#d62a22,#a51812 58%,rgba(255,255,255,0) 60%)" role="img" aria-label="Red chili peppers"></div>

  <div class="abs" style="left:140px;top:4790px;width:210px;text-align:center;font:500 21px/1.1 'Oswald',sans-serif;color:var(--white);text-transform:uppercase">Ember Plank Catering</div>

  <p class="footer-label" style="left:422px;top:4698px">Stay in the loop with special<br>offers and events.</p>
  <div class="footer-input">Enter Email</div>
  <div class="footer-signup">Sign Up</div>
  <span class="social" style="left:422px"></span>
  <span class="social" style="left:460px"></span>
  <span class="social" style="left:499px"></span>

  <p class="footer-label" style="left:825px;top:4698px">Contact Us</p>
  <svg class="abs" style="left:826px;top:4756px" width="16" height="12" viewBox="0 0 16 12" aria-hidden="true"><rect x="0" y="0" width="16" height="12" fill="#fff"/><path d="M0 0 L8 7 L16 0" fill="none" stroke="var(--brown)" stroke-width="1.6"/></svg>
  <p class="footer-contact" style="top:4750px">1235,Nemo enim ipsam volupt<br>atem quia voluptas sit</p>
  <svg class="abs" style="left:826px;top:4810px" width="16" height="16" viewBox="0 0 16 16" aria-hidden="true"><path d="M3 1 L6 1 L7 5 L5 6.5 Q6.5 9.5 9.5 11 L11 9 L15 10 L15 13 Q15 15 13 15 Q1 14 1 3 Q1 1 3 1 Z" fill="#fff"/></svg>
  <p class="footer-contact" style="top:4808px">+1 555 014 2870</p>

  <p class="footer-copy">©2024 Ember Plank Catering All Rights Reserved &nbsp;|&nbsp; Privacy &nbsp;|&nbsp; Terms of Use</p>
</div>
</body>
</html>
```